Local Chiropractor Needs Up Scale Webdesign

This website needs to have an upscale look with a very modern feel. Below is the information and websites to reference

Add Logo that is attached

Build a color scheme similar to this website image titled "chiro-1"

Must Include these pages in a horizontal menu bar in this order:
Home, Meet Our Staff, Patient Testimonials, Videos, Work Place Wellness, Contact

Build a "classy looking" Make An Appointment Button into the header with the contact info below

Phone Number:
555-314-2719

Address:
3168 Pelham Orchard Lane, #240
Willow Bend, MN 55390

This website needs 4 rotating banners. Please reference a layout similar to this for the banners: http://drmorlatz.example/. However design it nicer than this website, this website is very boring and doesn't flow with the colors properly

Below are the description for each banner

Rotating Banner #1
Use Image: Pediatrics
Two lines of text. First line title line, second description. Use Latin text for fill

Rotating Banner #2
Use Image: Aging Gracefully

Rotating Banner #3
Use Image: Pregnancy

Rotating Banner #4
Use Image: Athletics

I'd like to see a free consultation box similar to the "chiro-1" image. Fields to include are: First Name, Last Name, Phone Number, Comments.

For the body, please fill it with latin text. Please design a professional body layout. You can include a box in the right column for the hours

Office Hours
Monday: 8:00-11:00, 2:00-5:00
Tuesday: 8:30-11:00, 2:00-5:30
Wednesday: 8:00-11:00, 2:00-5:00
Thursday: 10:00-12:00, 2:30-5:00
Friday: 8:00-10:00, 1:00-5:00
Saturday: Closed
Sunday: Closed

For the footer please design something similar to the: http://drmorlatz.example/

Also include in the Footer: Powered by Brightline Site Works

```html
<!DOCTYPE html>
<html lang="en">
<head>
<meta charset="utf-8">
<title>Evergreen Vitality Chiropractic</title>
<link href="https://fonts.googleapis.com/css2?family=Lato:ital,wght@0,400;0,700;0,900;1,700;1,900&display=swap" rel="stylesheet">
<style>
:root{
  --green:#86bc25;
  --green-dark:#6a9a16;
  --header:#1f1f1f;
  --page:#1c1c1c;
  --strip:#262626;
  --panel:#202020;
  --line:#333;
  --text:#8a8a8a;
  --white:#fff;
  --footer-band:#2c2c2c;
}
*{box-sizing:border-box;margin:0;padding:0}
html,body{width:692px;height:1200px;overflow:hidden}
body{background:var(--page);font-family:'Lato',sans-serif;color:var(--text);position:relative;font-size:6px;line-height:1.55}
.abs{position:absolute}
.site-header{left:0;top:0;width:692px;height:65px;background:var(--header)}
.brand{left:93px;top:14px;display:flex;align-items:center;gap:5px;color:var(--white);font-weight:700;font-size:11px;line-height:1}
.brand-mark{width:14px;height:14px;border-radius:50%;background:var(--green)}
.brand small{display:block;font-size:5px;font-weight:400;color:var(--green);margin-top:2px}
.contact-item{top:15px;display:flex;gap:8px;align-items:flex-start;color:var(--white);font-size:5.5px;line-height:1.5}
.contact-item span{color:#777;display:block}
.contact-item svg{width:12px;height:12px;fill:#555;margin-top:1px}
.divider-v{top:13px;width:1px;height:22px;background:#333}
.btn-appointment{left:513px;top:13px;width:85px;height:22px;background:var(--green);color:var(--white);font-weight:900;font-size:5.5px;display:flex;align-items:center;justify-content:center;border-radius:2px;letter-spacing:.1px}
.main-nav{left:93px;top:49px;width:505px;height:32px;background:linear-gradient(#fff,#eee);display:flex;justify-content:center;align-items:center;z-index:3;box-shadow:0 1px 3px rgba(0,0,0,.3)}
.main-nav a{font-size:5.4px;color:#666;text-decoration:none;padding:0 7px;border-left:1px solid #ddd;position:relative;line-height:8px}
.main-nav a:first-child{border-left:0}
.main-nav a::before{content:"";position:absolute;left:50%;top:-9px;border:1.5px solid transparent;border-top-color:#888;margin-left:-1.5px}
.main-nav a.active{color:#222}
.main-nav a.active::before{border-top-color:var(--green)}
.hero{left:0;top:65px;width:692px;height:237px;background:linear-gradient(90deg,#8aa06a 0%,#d9e2c8 30%,#f0e6d8 55%,#d8b48c 75%,#c8c890 100%)}
.hero-caption{left:94px;top:137px;width:215px;height:112px;background:rgba(0,0,0,.55);padding:3px}
.hero-caption-inner{border:1px solid rgba(255,255,255,.6);height:100%;padding:8px 8px}
.hero-caption h1{color:var(--white);font-size:16px;font-weight:700;line-height:1.2}
.green-rule{width:22px;height:2px;background:var(--green);margin:6px 0}
.hero-caption p{color:#ddd;font-size:6px;line-height:1.65}
.slider-arrows{display:flex;gap:4px;margin-top:10px}
.slider-arrows span{width:22px;height:20px;background:var(--green);display:flex;align-items:center;justify-content:center}
.slider-arrows svg{width:6px;height:6px;stroke:#fff;fill:none;stroke-width:2}
.cta-strip{left:0;top:302px;width:692px;height:43px;background:var(--strip)}
.cta-strip p{position:absolute;left:93px;top:16px;color:var(--white);font-weight:900;font-style:italic;font-size:7px}
.btn-outline{left:533px;top:315px;width:65px;height:19px;border:1px solid #ccc;color:var(--white);font-weight:700;font-size:5.5px;display:flex;align-items:center;justify-content:center;gap:3px}
.about{left:93px;top:379px;width:331px}
.section-title{color:var(--white);font-weight:700;font-size:8px;line-height:1.2}
.subtitle{font-size:4.5px;color:#888;line-height:1.4}
.rule-row{position:relative;height:8px;border-bottom:1px solid var(--line);margin-bottom:4px}
.rule-row::before{content:"";position:absolute;left:0;bottom:-1px;width:21px;height:2px;background:var(--green)}
.about p{font-size:5.6px;line-height:1.95;margin-bottom:10px}
.tick-list{list-style:none;margin-top:18px}
.tick-list li{color:var(--white);font-weight:900;font-size:5.4px;display:flex;gap:4px;align-items:center;margin-bottom:8px}
.tick-list svg{width:6px;height:6px;stroke:var(--green);fill:none;stroke-width:2.5}
.card{top:607px;width:160px}
.card-media{height:94px;border:1px solid #555}
.card h3{color:var(--white);font-size:7px;font-weight:700;margin-top:9px}
.card.featured h3{color:var(--green)}
.card p{font-size:5.6px;line-height:1.95}
.read-more{color:var(--white);font-weight:700;font-size:5.5px;margin-top:6px}
.consult{left:439px;top:380px;width:159px;height:265px;border:1px solid var(--line);background:var(--panel)}
.consult-head{position:relative;height:61px;text-align:center;padding-top:7px}
.consult-head svg{position:absolute;left:0;top:0;width:159px;height:61px}
.consult-head *{position:relative}
.consult-head .kicker{color:var(--green);font-size:5.5px}
.consult-head h2{color:#222;font-size:9px;font-weight:700;margin-top:3px}
.consult-head .today{color:var(--green);font-size:5px;margin-top:3px}
.consult-body{padding:8px 8px}
.consult-body h4{color:var(--white);font-weight:900;font-size:7px;margin-bottom:9px}
.consult-body label{display:block;color:var(--white);font-weight:700;font-size:5.3px;margin-bottom:4px}
.field{height:13px;border:1px solid #333;background:#1a1a1a;margin-bottom:10px}
.field.focus{border-color:var(--green)}
.field.area{height:43px}
.btn-submit{width:55px;height:17px;background:var(--green);color:var(--white);font-weight:700;font-size:5.5px;display:flex;align-items:center;justify-content:center;margin-top:-2px}
.hours{left:439px;top:659px;width:159px;height:127px;border:1px solid var(--line);background:var(--panel)}
.hours h2{height:25px;background:var(--white);color:#222;font-size:7px;font-weight:700;text-align:center;line-height:25px}
.hours table{width:143px;margin:6px 8px;border-collapse:collapse}
.hours td{font-size:5px;height:13px;color:#888;text-align:right}
.hours td:first-child{text-align:left;color:var(--white);font-weight:700}
.hours tr.closed td{color:var(--green)}
.newsletter{left:93px;top:820px;width:505px;height:129px;border:6px solid #3a3a3a;background:var(--panel);text-align:center}
.newsletter-inner{border:1px solid #444;height:100%;padding-top:22px}
.newsletter h2{color:var(--white);font-weight:900;font-size:12px}
.newsletter p{font-size:5.8px;margin-top:4px}
.subscribe-row{display:flex;justify-content:center;margin-top:19px}
.subscribe-row .input{width:129px;height:19px;background:#181818;border:1px solid #333;display:flex;align-items:center;gap:6px;padding-left:8px;font-style:italic;font-size:5px;color:#666}
.subscribe-row svg{width:6px;height:6px;fill:#777}
.subscribe-row .btn{width:53px;height:19px;background:var(--green);color:#fff;font-weight:700;font-size:5.5px;display:flex;align-items:center;justify-content:center;margin-left:5px}
.footer-band{left:0;top:984px;width:692px;height:34px;background:var(--footer-band)}
.footer-band .brand{top:10px;font-size:9px}
.footer-band .brand-mark{width:11px;height:11px}
.social{position:absolute;right:94px;top:8px;display:flex;gap:4px}
.social span{width:17px;height:17px;background:#1c1c1c;border:1px solid #555}
.social span.on{background:var(--green);border-color:var(--green)}
.footer-col{top:1044px;font-size:5.5px}
.footer-col h5{color:var(--white);font-size:6.5px;font-weight:700;text-align:center;margin-bottom:16px}
.footer-col p{line-height:1.95}
.footer-links{display:flex;margin-top:10px;color:var(--white)}
.footer-links span{padding:0 8px;border-left:1px solid #444}
.footer-links span:first-child{padding-left:0;border-left:0}
.footer-links .hl{color:var(--green)}
.map{width:158px;height:67px;background:linear-gradient(135deg,#d8d8d8,#eceae6);border:2px solid #555}
.get-in-touch li{list-style:none;display:flex;gap:7px;align-items:center;margin-bottom:4px;padding-left:33px}
.get-in-touch svg{width:6px;height:6px;fill:#999}
.get-in-touch .addr{color:var(--white);font-weight:700;margin-bottom:10px;white-space:nowrap}
.bottom-bar{left:0;top:1166px;width:692px;height:34px;background:var(--green);color:var(--white);font-weight:700;font-size:5.4px}
.bottom-bar .credit{position:absolute;left:93px;top:13px}
.bottom-bar nav{position:absolute;right:118px;top:13px;display:flex}
.bottom-bar nav span{padding:0 7px;border-left:1px solid rgba(255,255,255,.6)}
.bottom-bar nav span:first-child{border-left:0}
.to-top{position:absolute;left:573px;top:9px;width:26px;height:16px;border:1px solid #fff;display:flex;align-items:center;justify-content:center}
.to-top svg{width:6px;height:6px;stroke:#fff;fill:none;stroke-width:1.6}
</style>
</head>
<body>

<header class="abs site-header">
  <div class="abs brand"><span class="brand-mark"></span><div>Evergreen Vitality<small>Chiropractic</small></div></div>
  <div class="abs contact-item" style="left:317px">
    <svg viewBox="0 0 24 24"><path d="M6.6 10.8a15 15 0 0 0 6.6 6.6l2.2-2.2a1 1 0 0 1 1-.25 11 11 0 0 0 3.6.6 1 1 0 0 1 1 1V20a1 1 0 0 1-1 1A17 17 0 0 1 3 4a1 1 0 0 1 1-1h3.5a1 1 0 0 1 1 1 11 11 0 0 0 .6 3.6 1 1 0 0 1-.25 1z"/></svg>
    <div>555-314-2719<span>info@example.com</span></div>
  </div>
  <div class="abs divider-v" style="left:393px"></div>
  <div class="abs contact-item" style="left:403px">
    <svg viewBox="0 0 24 24"><path d="M12 3 2 12h3v8h5v-6h4v6h5v-8h3z"/></svg>
    <div>Willow Bend, MN 55390<span>3168 Pelham Orchard Lane, #240</span></div>
  </div>
  <div class="abs btn-appointment">MAKE AN APPOINTMENT</div>
</header>

<nav class="abs main-nav">
  <a>HOME</a><a class="active">MEET OUR STAFF</a><a>PATIENT TESTIMONIALS</a><a>VIDEOS</a><a>WORK PLACE WELLNESS</a><a>CONTACT</a>
</nav>

<section class="abs hero" role="img" aria-label="Banner photo: smiling mother and young child outdoors in sunlight"></section>
<div class="abs hero-caption">
  <div class="hero-caption-inner">
    <h1>Your Title Goes Here</h1>
    <div class="green-rule"></div>
    <p>Lorem ipsum dolor sit amet, consectetur adipisicing elit, sed do eiusmod tempor incididunt ut labore et dolore magna aliqua.</p>
    <div class="slider-arrows">
      <span><svg viewBox="0 0 8 8"><path d="M5.5 1 2.5 4l3 3"/></svg></span>
      <span><svg viewBox="0 0 8 8"><path d="M2.5 1l3 3-3 3"/></svg></span>
    </div>
  </div>
</div>

<section class="abs cta-strip"><p>DONEC SUSCIPIT VEHICULA TURPIS SED LUTPAT QUISQUE VITAE QUAM NEQUE?</p></section>
<div class="abs btn-outline">Contact Us <svg width="6" height="5" viewBox="0 0 12 9" fill="none" stroke="#fff"><rect x=".5" y=".5" width="11" height="8"/><path d="M.5.5 6 5l5.5-4.5"/></svg></div>

<section class="abs about">
  <h2 class="section-title">Hello Dear Visitor</h2>
  <div class="subtitle">This is an About Us Text</div>
  <div class="rule-row" style="margin-top:4px"></div>
  <p>Pellentesque habitant morbi tristique senectus et netus et malesuada fames ac turpis egestas. Donec faucibus aliquet dui, nec congue orci sagittis eget. Sed sit amet augue id nisi fringilla elementum ut nec augue. Fusce ultrices convallis enim eu interdum. Nam libero neque, congue id nisl vel, sagittis malesuada ex. Ut vel arcu sed ligula condimentum con sequat sed vehicula purus. Donec eu erat pharetra, euismod justo id, volutpat orci. Etiam ac tortor ut urna egestas cursus vel nec nisi. Vivamus molestie nec magna sit amet rutrum.</p>
  <p>Nullam maximus tincidunt metus, quis tempus libero vulputate non. Ut vitae aliquam urna, pharetra elementum ipsum. Phasellus maximus dolor orci. Pellentesque leo tortor, hendrerit sit amet rutrum. Imperdiet vel ligula. Cum sociis natoque penatibus et magnis dis parturient montes, nascetur ridiculus mus.</p>
  <ul class="tick-list">
    <li><svg viewBox="0 0 8 8"><path d="M1 4l2 2 4-5"/></svg>SED NON MASSA SIT AMET ENIM FEUGIAT BIBENDUM A ET ARCU</li>
    <li><svg viewBox="0 0 8 8"><path d="M1 4l2 2 4-5"/></svg>CRAS ACCUMSAN TRISTIQUE EUISMOD. IN AC DIAM ET NULLA HENDRERIT</li>
    <li><svg viewBox="0 0 8 8"><path d="M1 4l2 2 4-5"/></svg>FUSCE EU TELLUS PHARETRA, ULTRICES DUI VITAE RHONCUS</li>
    <li><svg viewBox="0 0 8 8"><path d="M1 4l2 2 4-5"/></svg>NIBH. QUISQUE ID QUAM VELIT. MORBI MALESUADA LOREM A NISL MOLLIS TEMPUS</li>
  </ul>
</section>

<article class="abs card" style="left:93px">
  <div class="card-media" role="img" aria-label="Photo: two skiers on a snowy slope" style="background:linear-gradient(160deg,#e8ecef,#c9d0d6)"></div>
  <h3>Title Goes Here</h3>
  <div class="subtitle">This is Subtitle</div>
  <div class="rule-row"></div>
  <p>Placerat dapibus. Etiam ultrices nulla sed leo malesuada commodo bibendum orci vi verra. Sed rutrum dapibus feugiat. Iasellus et congue arcu.</p>
  <div class="read-more">Read More &#9758;</div>
</article>
<article class="abs card featured" style="left:266px">
  <div class="card-media" role="img" aria-label="Photo with green overlay: child playing" style="background:linear-gradient(135deg,#a5cc4a,#8ab82a);border-color:#8ab82a"></div>
  <h3>Title Goes Here</h3>
  <div class="subtitle">This is Subtitle</div>
  <div class="rule-row"></div>
  <p>Placerat dapibus. Etiam ultrices nulla sed leo malesuada commodo bibendum orci vi verra. Sed rutrum dapibus feugiat. Iasellus et congue arcu.</p>
  <div class="read-more" style="color:var(--green)">Read More &#9758;</div>
</article>

<aside class="abs consult">
  <div class="consult-head">
    <svg viewBox="0 0 159 61" preserveAspectRatio="none"><path d="M0 0H159V47L79.5 61 0 47z" fill="#fff"/></svg>
    <div class="kicker">CONTACT US NOW &amp; GET YOUR</div>
    <h2>FREE CONSULTATION</h2>
    <div class="today">&mdash;&mdash;&mdash;&mdash; TODAY ! &mdash;&mdash;&mdash;&mdash;</div>
  </div>
  <form class="consult-body">
    <h4>WELLNESS BEGINS HERE</h4>
    <label>First Name</label><div class="field"></div>
    <label>Last Name</label><div class="field focus"></div>
    <label>Phone Number</label><div class="field"></div>
    <label>Comments</label><div class="field area"></div>
    <div class="btn-submit">Submit &#9758;</div>
  </form>
</aside>

<aside class="abs hours">
  <h2>OPENING HOURS</h2>
  <table>
    <tr><td>Monday</td><td>8:00-11:00, 14:00-17:00</td></tr>
    <tr><td>Tuesday</td><td>8:30-11:00, 14:00-17:30</td></tr>
    <tr><td>Wednesday</td><td>8:00-11:00, 14:00-17:00</td></tr>
    <tr><td>Thursday</td><td>10:00-12:00, 14:30-17:00</td></tr>
    <tr><td>Friday</td><td>8:00-10:00, 13:00-17:00</td></tr>
    <tr class="closed"><td>Saturday</td><td>Closed</td></tr>
    <tr class="closed"><td>Sunday</td><td>Closed</td></tr>
  </table>
</aside>

<section class="abs newsletter">
  <div class="newsletter-inner">
    <h2>NEWSLETTER SUBSCRIPTION</h2>
    <p>Subscribe and be the first one who is getting the latest news &amp; notes! We promise to keep your mails safe, NO SPAMS!</p>
    <div class="subscribe-row">
      <div class="input"><svg viewBox="0 0 10 10"><path d="M1 7v2h2l5-5-2-2zM7 1l2 2 1-1-2-2z"/></svg>Enter Your Full Name</div>
      <div class="input"><svg viewBox="0 0 10 10"><path d="M0 2h10v6H0zM1 3l4 3 4-3"/></svg>Enter Your Email Address</div>
      <div class="btn">Subscribe</div>
    </div>
  </div>
</section>

<div class="abs footer-band">
  <div class="abs brand"><span class="brand-mark"></span>Evergreen Vitality</div>
  <div class="social"><span></span><span class="on"></span><span></span><span></span><span></span><span></span></div>
</div>

<div class="abs footer-col" style="left:93px;width:158px">
  <h5>- ABOUT US -</h5>
  <p>Phasellus rhoncus sapien ipsum, at sollicitudin nunc rhoncus quis. Mauris gravida neque clementum est imperdict, non vehicula risus finibus. Vivamus faucibus aliquet leo vitae laoreet. Cras commodo velit metus.</p>
  <div class="footer-links"><span>Privacy Policy</span><span class="hl">Terms and Conditions</span><span>FAQ</span></div>
</div>
<div class="abs footer-col" style="left:267px;width:158px">
  <h5>- WE ARE HERE -</h5>
  <div class="map" role="img" aria-label="Street map showing the office location"></div>
</div>
<div class="abs footer-col" style="left:440px;width:158px">
  <h5>- GET IN TOUCH -</h5>
  <ul class="get-in-touch">
    <li class="addr" style="padding-left:5px">3168 Pelham Orchard Lane, #240 Willow Bend, MN 55390</li>
    <li><svg viewBox="0 0 24 24"><path d="M6.6 10.8a15 15 0 0 0 6.6 6.6l2.2-2.2a1 1 0 0 1 1-.25 11 11 0 0 0 3.6.6 1 1 0 0 1 1 1V20a1 1 0 0 1-1 1A17 17 0 0 1 3 4a1 1 0 0 1 1-1h3.5a1 1 0 0 1 1 1 11 11 0 0 0 .6 3.6 1 1 0 0 1-.25 1z"/></svg>+1 555-314-2719</li>
    <li><svg viewBox="0 0 10 10"><path d="M2 0h6v3H2zM0 3h10v5H8v2H2V8H0z"/></svg>+1 555-314-2719</li>
    <li style="color:var(--green)"><svg viewBox="0 0 10 10"><path d="M0 2h10v6H0z"/></svg>info@example.com</li>
    <li><svg viewBox="0 0 10 10"><path d="M5 0a3.5 3.5 0 0 1 3.5 3.5C8.5 6 5 10 5 10S1.5 6 1.5 3.5A3.5 3.5 0 0 1 5 0z"/></svg>see in large map</li>
  </ul>
</div>

<footer class="abs bottom-bar">
  <div class="credit">Powered by Brightline Site Works &copy; Copyright 2015</div>
  <nav><span>Home</span><span>Meet Our Staff</span><span>Patient Testimonials</span><span>Videos</span><span>Work Place Wellness</span><span>Contact</span></nav>
  <div class="to-top"><svg viewBox="0 0 8 8"><path d="M1 5.5 4 2.5l3 3"/></svg></div>
</footer>

</body>
</html>
```